Flalzflyer-Design (Folder)
Da für uns neben einem guten Design ein angenehmer und konstruktiver Dialog sowie Verlässlichkeit von hoher Bedeutung ist, sind wir sehr froh auf dieser Plattform auf "brightloom" gestoßen zu sein. Wir sagen ganz herzlich DANKE!!
Zielgruppe
Zielgruppe im Bereich der Vermietung sind Alleinreisende oder als Paar verreisende Natur- und Nordsee verbundene Feriengäste (ü30) mit dem Urlaubsziel 'Sylt', welche eine persönlich und mit besonderem Schick eingerichtet Ferienwohnung/Ferienapartment in zentraler Lage in Westerland suchen und die es als positiven bzw. interessanten Aspekt sehen, dass die Ferienwohnungen direkt von uns Insulaner angeboten werden und wir als Sylter Familie ebenfalls Vor-Ort mit dem Urlaubern unter dem selben Dach leben (wenn auch nicht in der derselben Wohnung ;) ), ganz gemäß unserem Slogan 'Nordseeurlaub unter einem Dach mit Insulanern'
Aufgabenstellung
Es soll ein Falzflyer (Folder) mit Wickelfalz (siehe ggf. https://www.druckwerk-nord.de/werbemittel/folder.html) designed werden (4/4-farbig Euroskala). Bestehend aus einem Papier Format DIN A4 mit zwei Falzen, sodass sich bei Berücksichtigung von Vor- u. Rückseite 6 Seiten ergeben. Die wesentlichen Texte/Inhalte/Informationen, finden sich hier: https://www.quartiersuche-online.de/481926/ . Neben dem Ferienapartment 'Kompass' w ird von uns die Ferienwohnung 'Wadlen' (friesisch für Seestern) angeboten, ebenfalls im Morgenlicht Sylt HOUSE (EST. 2017).
Preisangaben können unberücksichtigt beliben, da sie dem Folder später über eine gesondere Einlage beigelegt werden sollen.
Im Rahmen des Dateiupload bei entwurfsmarkt werden nur einige der möglichen Fotos bereitgestellt. Sie sollen als Auswahlmöglichkeit dienen. Welche der Fotos Verwendung finden oder nach weiteren nachgefragt wird, soll in Abhängigkeit mit dem Gesamtdesign stehen und zunächst von Ihnen entschieden werden, um ein möglichst ansprechenden und harmonischen Folder kreieren zu können.

```html
<!DOCTYPE html>
<html lang="de">
<head>
<meta charset="utf-8">
<title>Morgenlicht Sylt HOUSE – Wickelfalz-Folder</title>
<link rel="stylesheet" href="https://fonts.googleapis.com/css2?family=Caveat:wght@400&family=Lato:wght@400;700&family=Arimo:wght@400;700&display=swap">
<style>
:root{
  --blue:#4c9fd3;
  --text:#555a5e;
  --heading:#4d5256;
  --rule:#bdbdbd;
  --stage:#d9d9d9;
  --paper:#ffffff;
  --sky:#6a9fd6;
  --sand:#cbb89a;
  --sea:#8fa6b4;
}
*{margin:0;padding:0;box-sizing:border-box}
html,body{width:1200px;height:3382px;overflow:hidden;background:var(--paper)}
body{position:relative;font-family:"Lato",sans-serif;color:var(--text)}
.abs{position:absolute}

/* stage with the flat cover */
.stage{position:absolute;left:0;top:0;width:1200px;height:808px;background:linear-gradient(180deg,#e2e2e2,var(--stage))}
.stage-cover{position:absolute;left:410px;top:28px;width:380px;height:752px;background:var(--paper);box-shadow:0 6px 22px rgba(0,0,0,.18)}

.separator{position:absolute;left:0;width:1200px;height:5px;background:var(--rule)}

.spread{position:absolute;left:0;width:1200px;height:814px}
.photo{position:absolute}
.photo-caption{position:absolute;right:8px;bottom:6px;font-family:"Caveat",cursive;font-size:17px;color:#fff}

/* photo tones */
.t-plant{background:linear-gradient(160deg,#b8d36a,#8fae4a 60%,#6d6a5a)}
.t-shelf{background:linear-gradient(180deg,#6e6453,#9b6b3e 55%,#5a4a3a)}
.t-fish{background:linear-gradient(135deg,#9c968e,#c9c4bc 50%,#7d776f)}
.t-mugs{background:linear-gradient(180deg,#d9dfe1,#7fb4c3 60%,#e9eef0)}
.t-window{background:linear-gradient(180deg,#a64a5c,#d9d3cf 45%,#4e5d74)}
.t-plate{background:radial-gradient(circle at 55% 50%,#f3eee6 30%,#bfb3a2 70%,#8e8274)}
.t-cotton{background:linear-gradient(160deg,#a79f92,#e8e3dc 55%,#c7a38a)}
.t-heart{background:linear-gradient(135deg,#cfcac2,#b8b3aa 50%,#2f6b84)}
.t-heart2{background:linear-gradient(135deg,#bfc3c3,#2f6b84 50%,#dfe3e3)}
.t-blinds{background:linear-gradient(180deg,#2c4f55,#d7dcda 50%,#6e7f62)}
.t-hall{background:linear-gradient(90deg,#e9e6de,#d6d0c2 55%,#8a7a2e)}
.t-table{background:linear-gradient(180deg,#3b3d40,#7a746b 60%,#b5ada1)}
.t-house{background:linear-gradient(180deg,#8fb3d9 0%,#e6e3de 35%,#c99c58 60%,#4f7a36 85%,#a35a4a)}
.t-hydr{background:linear-gradient(180deg,#5e6fa6,#8390c4 45%,#5e7a4a 80%,#9aa0a0)}
.t-sea{background:linear-gradient(180deg,#9fb0bf,#dde3e8 45%,#6f8595 75%,#8a9aa3)}
.t-beach{background:linear-gradient(180deg,#4f88d0 0%,#9fc2ea 30%,#e8edf2 45%,#3a63a1 62%,#d1c1a2 75%,#8b7d6a 100%)}
.t-room1{background:linear-gradient(160deg,#d7c7b0,#8a6a4e 60%,#4a3a2e)}
.t-room2{background:linear-gradient(160deg,#d9d4cb,#5a5d62 55%,#e8e2d4)}
.t-bed{background:linear-gradient(180deg,#e0ddd7,#c44c5a 55%,#efe9e1)}
.t-bath{background:linear-gradient(180deg,#eeeae4,#d2cdc4 60%,#4d5f44)}
.t-sand{background:linear-gradient(135deg,#cfc7b8,#a9a090 55%,#ddd6c8)}
.t-dunes{background:linear-gradient(180deg,#6f9fd8 0%,#cfe0f0 40%,#6d8aa2 55%,#b79f6c 75%,#7f8a4a)}
.t-shore{background:linear-gradient(180deg,#3e78b8,#b9d0e6 45%,#8aa0b0 65%,#d7cfc0)}
.t-sunset{background:linear-gradient(180deg,#2d3d5c,#e0894a 55%,#3a2c26)}
.t-plan{background:#eef1f4;border:1px solid #9aa4ad}
.t-plan-pink{background:linear-gradient(180deg,#f4c8bb,#eab3a4);border:1px solid #9aa4ad}

/* column type */
.script{font-family:"Caveat",cursive;color:var(--blue);font-weight:400;line-height:1}
.col-heading{font-family:"Lato",sans-serif;font-size:22px;line-height:28px;color:var(--heading);font-weight:700;letter-spacing:.2px}
.col-heading span{font-weight:400;display:block}
.body-copy{font-family:"Lato",sans-serif;font-size:12.6px;line-height:19.5px;color:var(--text)}
.body-copy p+p{margin-top:11px}
.dash-rule{height:0;border-top:2px dashed var(--blue)}
.contact{font-family:"Lato",sans-serif;font-size:12.6px;line-height:18.4px;color:var(--text)}
.contact b{font-weight:700}

.feature-title{font-size:34px;text-align:center;white-space:nowrap}
.feature-sub{font-size:18px;color:var(--blue);text-align:center;letter-spacing:.5px}

.cover-tag{font-size:35px;text-align:center;white-space:nowrap}
.cover-name{font-size:19px;font-weight:700;color:var(--heading);text-align:center}
.cover-est{font-size:15px;color:var(--heading);text-align:center}
.cover-welcome{font-size:24px;line-height:28px;color:var(--heading);text-align:center;letter-spacing:.3px}
.cover-welcome b{font-weight:700}

/* inside spread */
.inside-title{font-size:35px;white-space:nowrap}
.inside-copy{font-family:"Arimo",sans-serif;font-size:12.4px;line-height:18.4px;color:var(--text)}
.inside-copy p+p{margin-top:14px}
.inside-copy b{font-weight:700}
.amenities{position:absolute;display:flex;justify-content:space-between}
.amenity{width:70px;text-align:center;font-family:"Arimo",sans-serif;font-size:9.5px;line-height:12px;color:var(--text)}
.amenity svg{display:block;margin:0 auto 8px;width:52px;height:52px}
</style>
</head>
<body>

<!-- cover shown flat on a plain stage -->
<section class="stage">
  <div class="stage-cover">
    <div class="photo t-beach" style="left:0;top:0;width:380px;height:430px" role="img" aria-label="Foto: Strand auf Sylt mit Rettungsturm, Fahne und blau-weißen Strandkörben hinter Dünengras"></div>
    <div class="abs script cover-tag" style="left:0;top:458px;width:380px">Nordseeurlaub bei Insulanern</div>
    <div class="abs cover-name" style="left:0;top:504px;width:380px">Morgenlicht Sylt HOUSE</div>
    <div class="abs cover-est" style="left:0;top:528px;width:380px">(EST. 2017)</div>
    <div class="abs cover-welcome" style="left:0;top:590px;width:380px">HERZLICH WILLKOMMEN<br><b>BEI FAMILIE MORGENLICHT!</b></div>
  </div>
</section>

<!-- outside spread, version 1 -->
<section class="spread" style="top:827px">
  <div class="photo t-plant" style="left:18px;top:0;width:124px;height:175px" role="img" aria-label="Foto: Blumenkorb vor grüner Wand"></div>
  <div class="photo t-shelf" style="left:146px;top:0;width:228px;height:175px" role="img" aria-label="Foto: Holzregal mit Deko-Buchstaben und Vogelfigur"></div>
  <div class="photo t-fish" style="left:18px;top:180px;width:231px;height:175px" role="img" aria-label="Foto: Fischdekoration an der Wand mit Windlicht"></div>
  <div class="photo t-mugs" style="left:253px;top:180px;width:121px;height:175px" role="img" aria-label="Foto: Tassen und Geschirr im Glasregal"></div>
  <div class="abs script feature-title" style="left:18px;top:378px;width:356px">Gemütlich &amp; mit Liebe</div>
  <div class="abs feature-sub" style="left:18px;top:414px;width:356px">ZUM DETAIL EINGERICHTET</div>
  <div class="photo t-window" style="left:18px;top:460px;width:238px;height:174px" role="img" aria-label="Foto: Fenster mit Raffrollo und Sitzbank"></div>
  <div class="photo t-plate" style="left:260px;top:460px;width:114px;height:174px" role="img" aria-label="Foto: Dekoteller an der Wand"></div>
  <div class="photo t-cotton" style="left:18px;top:640px;width:145px;height:174px" role="img" aria-label="Foto: Baumwollzweig in einer Tasse"></div>
  <div class="photo t-heart" style="left:168px;top:640px;width:206px;height:174px" role="img" aria-label="Foto: Gestricktes blaues Herz als Deko"></div>

  <div class="photo t-house" style="left:414px;top:0;width:177px;height:325px" role="img" aria-label="Foto: Hausansicht mit Klinkerweg und Garten"></div>
  <div class="photo t-hydr" style="left:595px;top:0;width:177px;height:158px" role="img" aria-label="Foto: Hortensien und Tassen auf dem Gartentisch"></div>
  <div class="photo t-sea" style="left:595px;top:163px;width:177px;height:162px" role="img" aria-label="Foto: Schwimmer in der Nordsee"><span class="photo-caption">Unsere 'Meerwasser-Schwimmanlage'</span></div>
  <h2 class="abs col-heading" style="left:414px;top:348px;width:361px">BESUCHEN SIE UNS<span>AUF SYLT.</span></h2>
  <div class="abs body-copy" style="left:414px;top:412px;width:361px">
    <p>Das Morgenlicht Sylt House (est. 2017) ist in Nachbarschaft des denkmalgeschützten Westerländer Polizeigebäudes (ehem. Amtsgericht) gelegen. Die vorteilhafte Lage ist damit zentral aber ruhig in 2. Reihe in Alt-Westerland.</p>
    <p>Der Bahnhof ist ca. 4-5 Gehminuten, die Fußgängerzone/Friedrichstr. mit div. Einkaufsmöglichkeiten und Restaurants/Cafés ca. 7 Min. und der Strand/die Kurpromenade ca. 12 Min. entfernt. Auch das Schwimmbad Brandungsbad, das Vitalzentrum Dünenkraft (Wellness) o. die Spielbank sind nah.</p>
  </div>
  <div class="abs dash-rule" style="left:414px;top:623px;width:361px"></div>
  <div class="abs contact" style="left:414px;top:636px;width:370px">
    Familie Morgenlicht<br><b>Morgenlicht Sylt HOUSE (EST. 2017)</b><br>Dünenpfad 14b, Westerland<br><br>
    <b>Wir sind für Sie da</b> · Mo - So &nbsp; 9.00 - 21.00<br>
    Telefon: +49 (0)4651 - 555 0192 · Mobil: +49 (0)172 - 555 0147<br>
    eMail: sylt@morgenlicht-haus.net<br>
    Belegungskalender: belegung.morgenlicht-haus.net<br>
    Mehr Fotos + Preise finden Sie auf: quartiersuche-online.de<br>
    =&gt; Wohin: Morgenlicht Sylt
  </div>

  <div class="photo t-beach" style="left:811px;top:0;width:368px;height:538px" role="img" aria-label="Foto: Strand auf Sylt mit Rettungsturm, Fahne und blau-weißen Strandkörben hinter Dünengras"></div>
  <div class="abs script cover-tag" style="left:811px;top:578px;width:368px">Nordseeurlaub bei Insulanern</div>
  <div class="abs cover-name" style="left:811px;top:626px;width:368px">Morgenlicht Sylt HOUSE</div>
  <div class="abs cover-est" style="left:811px;top:649px;width:368px">(EST. 2017)</div>
  <div class="abs cover-welcome" style="left:811px;top:708px;width:368px">HERZLICH WILLKOMMEN<br><b>BEI FAMILIE MORGENLICHT!</b></div>
</section>

<div class="separator" style="top:1659px"></div>

<!-- outside spread, version 2 -->
<section class="spread" style="top:1687px">
  <div class="photo t-heart2" style="left:18px;top:0;width:127px;height:175px" role="img" aria-label="Foto: Gestricktes blaues Herz auf weißer Kommode"></div>
  <div class="photo t-shelf" style="left:148px;top:0;width:226px;height:175px" role="img" aria-label="Foto: Holzregal mit Deko-Buchstaben und Vogelfigur"></div>
  <div class="photo t-blinds" style="left:18px;top:180px;width:231px;height:172px" role="img" aria-label="Foto: Fenster mit Jalousie und Blick ins Grüne"></div>
  <div class="photo t-mugs" style="left:253px;top:180px;width:121px;height:172px" role="img" aria-label="Foto: Tassen und Geschirr im Glasregal"></div>
  <div class="abs script feature-title" style="left:18px;top:387px;width:356px">Details zum Wohlfühlen</div>
  <div class="photo t-cotton" style="left:18px;top:460px;width:238px;height:174px" role="img" aria-label="Foto: Baumwollzweig in einer Tasse"></div>
  <div class="photo t-plant" style="left:260px;top:460px;width:114px;height:174px" role="img" aria-label="Foto: Blumenkorb vor grüner Wand"></div>
  <div class="photo t-hall" style="left:18px;top:640px;width:145px;height:174px" role="img" aria-label="Foto: Flur mit hängendem Dekoherz"></div>
  <div class="photo t-table" style="left:168px;top:640px;width:206px;height:174px" role="img" aria-label="Foto: Holztisch mit Windlicht"></div>

  <div class="photo t-house" style="left:414px;top:0;width:177px;height:325px" role="img" aria-label="Foto: Hausansicht mit Klinkerweg und Garten"></div>
  <div class="photo t-hydr" style="left:595px;top:0;width:177px;height:158px" role="img" aria-label="Foto: Hortensien und Tassen auf dem Gartentisch"></div>
  <div class="photo t-sea" style="left:595px;top:163px;width:177px;height:162px" role="img" aria-label="Foto: Schwimmer in der Nordsee"><span class="photo-caption">Unsere 'Meerwasser-Schwimmanlage'</span></div>
  <h2 class="abs col-heading" style="left:414px;top:348px;width:361px">BESUCHEN SIE UNS<span>AUF SYLT.</span></h2>
  <div class="abs body-copy" style="left:414px;top:412px;width:361px">
    <p>Das Morgenlicht Sylt House (est. 2017) ist in Nachbarschaft des denkmalgeschützten Westerländer Polizeigebäudes (ehem. Amtsgericht) gelegen. Die vorteilhafte Lage ist damit zentral aber ruhig in 2. Reihe in Alt-Westerland.</p>
    <p>Der Bahnhof ist ca. 4-5 Gehminuten, die Fußgängerzone/Friedrichstr. mit div. Einkaufsmöglichkeiten und Restaurants/Cafés ca. 7 Min. und der Strand/die Kurpromenade ca. 12 Min. entfernt. Auch das Schwimmbad Brandungsbad, das Vitalzentrum Dünenkraft (Wellness) o. die Spielbank sind nah.</p>
  </div>
  <div class="abs dash-rule" style="left:414px;top:623px;width:361px"></div>
  <div class="abs contact" style="left:414px;top:636px;width:370px">
    Familie Morgenlicht<br><b>Morgenlicht Sylt HOUSE (EST. 2017)</b><br>Dünenpfad 14b, Westerland<br><br>
    <b>Wir sind für Sie da</b> · Mo - So &nbsp; 9.00 - 21.00<br>
    Telefon: +49 (0)4651 - 555 0192 · Mobil: +49 (0)172 - 555 0147<br>
    eMail: sylt@morgenlicht-haus.net<br>
    Belegungskalender: belegung.morgenlicht-haus.net<br>
    Mehr Fotos + Preise finden Sie auf: quartiersuche-online.de<br>
    =&gt; Wohin: Morgenlicht Sylt
  </div>

  <div class="photo t-beach" style="left:811px;top:0;width:368px;height:538px" role="img" aria-label="Foto: Strand auf Sylt mit Rettungsturm, Fahne und blau-weißen Strandkörben hinter Dünengras"></div>
  <div class="abs script cover-tag" style="left:811px;top:578px;width:368px">Nordseeurlaub bei Insulanern</div>
  <div class="abs cover-name" style="left:811px;top:626px;width:368px">Morgenlicht Sylt HOUSE</div>
  <div class="abs cover-est" style="left:811px;top:649px;width:368px">(EST. 2017)</div>
  <div class="abs cover-welcome" style="left:811px;top:708px;width:368px">HERZLICH WILLKOMMEN<br><b>BEI FAMILIE MORGENLICHT!</b></div>
</section>

<div class="separator" style="top:2519px"></div>

<!-- inside spread -->
<section class="spread" style="top:2540px;height:842px">
  <!-- apartment Kompass -->
  <h3 class="abs script inside-title" style="left:20px;top:22px">Ferienapartment 'Kompass'</h3>
  <div class="photo t-room1" style="left:20px;top:73px;width:184px;height:173px" role="img" aria-label="Foto: Apartment mit Holzschrank und Stehlampe"></div>
  <div class="photo t-room2" style="left:207px;top:73px;width:180px;height:173px" role="img" aria-label="Foto: Wohnbereich mit Sofa und Kissen"></div>
  <div class="abs inside-copy" style="left:20px;top:262px;width:367px">Das Apartment ist seniorengerecht, ebenerdig, kurze Wege, Ansprechpartner im Haus, Bahnhof Westerland fussläufig 5 Min.</div>
  <div class="photo t-plan" style="left:29px;top:312px;width:332px;height:170px" role="img" aria-label="Grundriss des Apartments Kompass im Erdgeschoss mit Außenbereich"></div>
  <div class="abs inside-copy" style="left:20px;top:500px;width:367px">
    <p><b>Wer Meer hat, braucht weniger, sagt man.</b><br>Die Zimmer persönlich und mit Geschick gestaltet, zeitgemäße Wohneinrichtung, modernes ebenerdiges Duschbad, hochwertige Pantryküche, Smart-TV, Wlan, ansprechendes und vollständiges Geschirr, Außenbereich sowie der persönlichen Nähe zu uns Insulanern.</p>
    <p>Das App. eignet sich für einen längeren Urlaub besonders für 1 Person. Es steht ein Einzelbett im kl. Schlafzimmer zur Verfügung. Für einen Aufenthalt von einigen Tagen haben 2 Pers. ebenfalls eine passend schöne Unterkunft (Schlafmöglichkeit auf komfortablen Schlafsofa mit Lattenrost).</p>
  </div>
  <div class="amenities" style="left:14px;top:738px;width:372px">
    <div class="amenity"><svg viewBox="0 0 52 52" fill="none" stroke="var(--blue)" stroke-width="3"><circle cx="26" cy="26" r="24"/><path d="M14 23a17 17 0 0 1 24 0M18 28a11 11 0 0 1 16 0M22 33a5 5 0 0 1 8 0" stroke-linecap="round"/><circle cx="26" cy="37" r="1.6" fill="var(--blue)"/></svg>kostenloses WLAN</div>
    <div class="amenity"><svg viewBox="0 0 52 52" fill="none" stroke="var(--blue)" stroke-width="3"><circle cx="26" cy="26" r="24"/><rect x="12" y="27" width="24" height="5"/><path d="M39 27v5M42 27v5M38 22c0-4 4-4 4-8"/><path d="M12 14l28 26" stroke-linecap="round"/></svg>Nichtraucher Wohnung</div>
    <div class="amenity"><svg viewBox="0 0 52 52" fill="none" stroke="var(--blue)" stroke-width="3"><circle cx="26" cy="26" r="24"/><path d="M15 38V18a11 6 0 0 1 22 0v20M15 28h22M15 38h22M20 22v6M26 22v6M32 22v6"/></svg>Strandkorb vorhanden</div>
    <div class="amenity"><svg viewBox="0 0 52 52" fill="none" stroke="var(--blue)" stroke-width="3"><circle cx="26" cy="26" r="24"/><rect x="15" y="13" width="22" height="26" rx="2"/><path d="M15 19h22"/><circle cx="26" cy="29" r="6"/></svg>Geschirrspüler vorhanden</div>
    <div class="amenity"><svg viewBox="0 0 52 52" fill="none" stroke="var(--blue)" stroke-width="3"><circle cx="26" cy="26" r="24"/><path d="M12 18v18M12 30h28v6M40 36v-9a4 4 0 0 0-4-4H24v7"/><circle cx="18" cy="26" r="3"/></svg>Bettwäsche &amp; Handtücher</div>
  </div>

  <!-- about us -->
  <h3 class="abs script inside-title" style="left:427px;top:22px">Wer sind wir</h3>
  <div class="abs inside-copy" style="left:427px;top:76px;width:358px">Wir sind eine 3-köpfige Familie, die ganzjährig im Morgenlicht Sylt HOUSE (Est. 2017) lebt und auf Wunsch gerne helfend mit Urlaubstipps und Klönschnack zur Verfügung steht. Unsere Tochter geht in Westerland zur Schule.</div>
  <h3 class="abs script inside-title" style="left:427px;top:168px">Warum sind wir Gastgeber</h3>
  <div class="abs inside-copy" style="left:427px;top:225px;width:358px">Weil wir als offene Menschen neue Begegnungen schätzen und so unseren Traum - ganzjährig auf Sylt zu leben - in die Tat umsetzen können.</div>
  <div class="photo t-sand" style="left:427px;top:283px;width:115px;height:190px" role="img" aria-label="Foto: In den Sand geschriebene Buchstaben"></div>
  <div class="photo t-dunes" style="left:548px;top:283px;width:237px;height:180px" role="img" aria-label="Foto: Blick von der Düne auf Strand und Meer"></div>
  <div class="photo t-shore" style="left:427px;top:479px;width:214px;height:126px" role="img" aria-label="Foto: Weiter Sandstrand mit Spaziergängern"></div>
  <div class="photo t-sunset" style="left:646px;top:469px;width:139px;height:136px" role="img" aria-label="Foto: Sonnenuntergang über der Nordsee"></div>
  <h3 class="abs script inside-title" style="left:427px;top:640px">Unser Service für Sie</h3>
  <div class="abs inside-copy" style="left:427px;top:694px;width:358px">
    <p>Kostenloser Hol-/Bringservice Bahnhof Westerland nach Absprache möglich.</p>
    <p>Das Wäschepaket beinhaltet: Bettwäsche, Laken, Handtuch (2x), Duschtuch, Badvorleger, Geschirrtuch.</p>
    <p>Endreinigung inklusive.</p>
  </div>

  <!-- apartment Wadlen -->
  <h3 class="abs script inside-title" style="left:827px;top:22px">Ferienwohnung 'Wadlen'</h3>
  <div class="photo t-bed" style="left:827px;top:73px;width:173px;height:173px" role="img" aria-label="Foto: Schlafzimmer mit Bett und Fenster"></div>
  <div class="photo t-bath" style="left:1006px;top:73px;width:172px;height:173px" role="img" aria-label="Foto: Modernes Duschbad mit WC"></div>
  <div class="abs inside-copy" style="left:827px;top:262px;width:352px">Das Apartment ist seniorengerecht, ebenerdig, kurze Wege, Ansprechpartner im Haus, Bahnhof Westerland fussläufig.</div>
  <div class="photo t-plan-pink" style="left:903px;top:312px;width:196px;height:175px" role="img" aria-label="Grundriss der Ferienwohnung Wadlen im Obergeschoss"></div>
  <div class="abs inside-copy" style="left:827px;top:500px;width:352px">
    <p><b>Wer Meer hat, braucht weniger, sagt man.</b><br>Die Zimmer persönlich und mit Geschick gestaltet, zeitgemäße Wohneinrichtung, modernes ebenerdiges Duschbad, hochwertige Pantryküche, Smart-TV, Wlan, ansprechendes und vollständiges Geschirr, Außenbereich sowie der persönlichen Nähe zu uns Insulanern.</p>
    <p>Das App. eignet sich für einen längeren Urlaub besonders für 1 Person. Es steht ein Einzelbett im kl. Schlafzimmer zur Verfügung. Für einen Aufenthalt von einigen Tagen haben 2 Pers. ebenfalls eine passend schöne Unterkunft (Schlafmöglichkeit auf komfortablen Schlafsofa mit Lattenrost).</p>
  </div>
  <div class="amenities" style="left:820px;top:730px;width:362px">
    <div class="amenity"><svg viewBox="0 0 52 52" fill="none" stroke="var(--blue)" stroke-width="3"><circle cx="26" cy="26" r="24"/><path d="M14 23a17 17 0 0 1 24 0M18 28a11 11 0 0 1 16 0M22 33a5 5 0 0 1 8 0" stroke-linecap="round"/><circle cx="26" cy="37" r="1.6" fill="var(--blue)"/></svg>kostenloses WLAN</div>
    <div class="amenity"><svg viewBox="0 0 52 52" fill="none" stroke="var(--blue)" stroke-width="3"><circle cx="26" cy="26" r="24"/><rect x="12" y="27" width="24" height="5"/><path d="M39 27v5M42 27v5M38 22c0-4 4-4 4-8"/><path d="M12 14l28 26" stroke-linecap="round"/></svg>Nichtraucher Wohnung</div>
    <div class="amenity"><svg viewBox="0 0 52 52" fill="none" stroke="var(--blue)" stroke-width="3"><circle cx="26" cy="26" r="24"/><rect x="13" y="15" width="26" height="17" rx="1.5"/><path d="M22 38h8M26 32v6"/></svg>Smart TV vorhanden</div>
    <div class="amenity"><svg viewBox="0 0 52 52" fill="none" stroke="var(--blue)" stroke-width="3"><circle cx="26" cy="26" r="24"/><rect x="15" y="13" width="22" height="26" rx="2"/><path d="M15 19h22"/><circle cx="26" cy="29" r="6"/></svg>Geschirrspüler vorhanden</div>
    <div class="amenity"><svg viewBox="0 0 52 52" fill="none" stroke="var(--blue)" stroke-width="3"><circle cx="26" cy="26" r="24"/><path d="M12 18v18M12 30h28v6M40 36v-9a4 4 0 0 0-4-4H24v7"/><circle cx="18" cy="26" r="3"/></svg>Bettwäsche &amp; Handtücher</div>
  </div>
</section>

</body>
</html>
```